Grey Fennel Medical Website to make connecting and communicating easier

To create a unique, user-friendly, professional website for patients and professionals to access education/ information, forms, appointments, contact details, and data about us, and for us to have the capacity to link to various cloud-based platforms.
To use the logo design and colour scheme we have just sourced.

WEBSITE to be eye catching, Inspiring and alluring
- efficient and logical
- professional and trustworthy appearance
- health focus "living health matters"
- user friendly
- ability to link with cloud-based software and video conferencing tools/ telehealth
- colours- black/ white teal and ?silver

PAGES:
page 1 - Our clinic and staff, services offered, contact us- address/ map / contact details- social media connections
page 2- patients and visitors - New patient forms to complete, news and patient informtion (educatinal)
page 3 - health professionals -referral forms, research and education
page 3- online appointments
page 4 - Quick links - partners, other services
page 5- privacy policy, disclaimer

HI, Could we please extend the deadline another 5 days, so sorry just struggling with my workload to be able to keep up and I am wanting to liaise more with the designer that I will choose. I am so happy with SketchHarbor and all the designers - thank you! Thank you so much!!

Target Market(s)

Patients - mostly over 60's so the website must be minimal clicks and simple to navigate
Professionals - for education and access forms

Industry/Entity Type

Health Care

Coding

Coded - Design and coding required

Number of Pages Required

5+ page

Font styles to use
Sans Serif
Script

Colors
33b8a4
86cfc6

Requirements
Must have
• WEBSITE to be eye catching, Inspiring and alluring
- efficient and logical
- user friendly

WEBSITE - professional and user friendly
- ability to link with cloud based software and videoconferencing/ telehealth
Nice to have
• clean and crisp presentation
happy for an innovative look
room to add more services and ability to link pages and resources
Should not have
• Please ensure the website is not:
clunky
difficult to navigate
common and cheap looking

```html
<!DOCTYPE html>
<html lang="en">
<head>
<meta charset="utf-8">
<title>Grey Fennel Medical</title>
<link href="https://fonts.googleapis.com/css2?family=Lato:wght@400;700;900&display=swap" rel="stylesheet">
<style>
:root{
  --teal:#2aa693;
  --teal-light:#86cfc6;
  --ink:#2b2b2b;
  --text:#444;
  --grey:#ececec;
  --white:#fff;
}
*{margin:0;padding:0;box-sizing:border-box}
html,body{width:1200px;height:3203px;overflow:hidden}
body{position:relative;background:var(--white);font-family:'Lato',sans-serif;color:var(--text)}
.abs{position:absolute}
.btn{position:absolute;display:flex;align-items:center;justify-content:center;background:var(--teal);color:#fff;font-weight:700;font-size:14px;letter-spacing:.3px;text-transform:uppercase;border-radius:3px;text-decoration:none}

/* header */
.site-header{left:0;top:0;width:1200px;height:118px;background:#fff}
.brand{display:flex;align-items:center;gap:10px;color:var(--teal);font-weight:900;font-size:22px;white-space:nowrap}
.brand-dot{width:34px;height:34px;border-radius:50%;background:var(--teal)}
.main-nav a{position:absolute;top:53px;font-size:14px;font-weight:700;color:var(--ink);text-decoration:none;white-space:nowrap}
.main-nav a.active{color:var(--teal)}

/* hero */
.hero-photo{left:0;top:118px;width:1200px;height:700px;background:linear-gradient(100deg,#b79a86 0%,#cfc6bf 30%,#dfe3e6 55%,#c8cfd2 75%,#8a9a86 100%)}
.hero-title{left:75px;top:380px;font-size:57px;font-weight:900;color:#fff;white-space:nowrap}
.hero-sub{left:75px;top:445px;font-size:22px;font-weight:700;color:#fff;white-space:nowrap}

/* clinic */
.staff-photo{left:73px;top:853px;width:500px;height:500px;border-radius:50%;background:radial-gradient(circle at 45% 35%,#f1e6df 0%,#dfe4ea 45%,#aebccb 100%)}
.section-title{font-size:52px;font-weight:700;color:var(--ink);white-space:nowrap}
.clinic-copy{left:614px;top:1037px;width:512px;font-size:17px;line-height:30.5px}

/* services */
.services-card{left:75px;top:1459px;width:1052px;height:555px;background:#fff;box-shadow:0 2px 10px rgba(0,0,0,.12)}
.service{position:absolute;top:0;width:320px;text-align:center}
.service-icon{width:90px;height:90px;border:2px solid var(--ink);border-radius:50%;margin:0 auto;display:flex;align-items:center;justify-content:center}
.service h3{margin-top:22px;font-size:26px;color:var(--teal);font-weight:700}
.service p{margin-top:6px;font-size:15.5px;line-height:26px}
.slider-arrow{width:82px;height:82px;border-radius:50%;background:#2c2c2c;display:flex;align-items:center}
.slider-arrow.prev{justify-content:flex-start;padding-left:16px}
.slider-arrow.next{justify-content:flex-end;padding-right:16px}

/* contact */
.map{left:628px;top:2295px;width:472px;height:472px;border-radius:50%;background:radial-gradient(circle at 50% 45%,#eae6da 0%,#dfe3e4 50%,#b9dcc0 100%)}
.contact-line{display:flex;align-items:center;gap:14px;font-size:17px;white-space:nowrap}

/* footer */
.footer-col h4{font-size:19px;font-weight:700;color:var(--ink);margin-bottom:6px}
.footer-col a{display:block;font-size:14.5px;color:var(--ink);line-height:29.5px;text-decoration:none}
.social{display:flex;gap:18px}
.social span{width:26px;height:26px;border-radius:50%;background:var(--ink)}
.fine{font-size:13.5px;line-height:24px;color:var(--ink)}
</style>
</head>
<body>

<header class="site-header abs">
  <div class="brand abs" style="left:77px;top:42px"><span class="brand-dot"></span>Grey Fennel Medical</div>
  <nav class="main-nav">
    <a class="active" style="left:439px">HOME</a>
    <a style="left:522px">ABOUT US</a>
    <a style="left:633px">SERVICES</a>
    <a style="left:737px">NEWS</a>
    <a style="left:818px">CONTACT US</a>
  </nav>
  <a class="btn" style="left:938px;top:43px;width:189px;height:37px;font-size:13px">Online Appointments</a>
</header>

<section class="hero">
  <div class="hero-photo abs" role="img" aria-label="Photo of a smiling doctor greeting an older patient"></div>
  <svg class="abs" style="left:0;top:660px" width="1200" height="170" viewBox="0 0 1200 170">
    <path d="M0 95 C150 150 280 160 400 130 C600 80 800 85 960 90 C1080 95 1150 80 1200 25 L1200 170 L0 170Z" fill="var(--grey)"/>
    <path d="M0 110 C150 165 290 170 420 140 C620 100 820 100 980 110 C1090 115 1160 95 1200 80 L1200 170 L0 170Z" fill="#fff"/>
  </svg>
  <h1 class="hero-title abs">Grey Fennel Medical</h1>
  <p class="hero-sub abs">Error sit voluptatem accusantium.</p>
  <a class="btn" style="left:75px;top:492px;width:235px;height:42px">Online Appointments</a>
</section>

<section class="clinic">
  <div class="staff-photo abs" role="img" aria-label="Photo of a smiling female doctor with a stethoscope"></div>
  <h2 class="section-title abs" style="left:614px;top:962px">Our Clinic &amp; Staff</h2>
  <p class="clinic-copy abs">Aliquam venenatis lacus vitae neque gravida, eget cursus ante semper. Nam urna nisl, congue et aliquet sit amet, pulvinar sit amet tortor. Etiam rutrum massa et lectus &nbsp;tincidunt, lacinia lobortis sapien malesuada. Mauris ac sodales odio posuere, enim eget vestibulum volutpat...</p>
  <a class="btn" style="left:614px;top:1219px;width:181px;height:42px">Read More</a>
</section>

<section class="services">
  <svg class="abs" style="left:0;top:1602px" width="1200" height="640" viewBox="0 0 1200 640">
    <defs><linearGradient id="band" x1="0" x2="1"><stop offset="0" stop-color="#2aa693"/><stop offset="1" stop-color="#86cfc6"/></linearGradient></defs>
    <path d="M0 0 H1200 V500 C1100 600 950 630 800 595 C600 545 450 500 300 495 C150 490 60 505 0 530Z" fill="url(#band)"/>
    <path d="M0 530 C60 505 150 490 300 495 C450 500 600 545 800 595 C950 630 1100 600 1200 500 V520 C1100 620 950 640 800 615 C600 570 450 545 300 540 C160 535 60 555 0 575Z" fill="var(--grey)"/>
  </svg>
  <div class="slider-arrow prev abs" style="left:30px;top:1678px"><svg width="22" height="22" viewBox="0 0 22 22"><path d="M14 3 L6 11 L14 19" stroke="#fff" stroke-width="3.5" fill="none"/></svg></div>
  <div class="slider-arrow next abs" style="left:1088px;top:1678px"><svg width="22" height="22" viewBox="0 0 22 22"><path d="M8 3 L16 11 L8 19" stroke="#fff" stroke-width="3.5" fill="none"/></svg></div>

  <div class="services-card abs">
    <h2 class="section-title abs" style="left:0;width:1052px;text-align:center;top:46px;font-size:50px">Our Services</h2>
    <div class="service" style="left:17px;top:146px">
      <div class="service-icon"><svg width="44" height="36" viewBox="0 0 44 36"><rect x="2" y="4" width="20" height="30" fill="#2b2b2b"/><rect x="7" y="10" width="4" height="4" fill="#fff"/><rect x="13" y="10" width="4" height="4" fill="#fff"/><rect x="7" y="18" width="4" height="4" fill="#fff"/><rect x="13" y="18" width="4" height="4" fill="#fff"/><circle cx="32" cy="15" r="6" fill="#2b2b2b"/><path d="M22 34 C22 24 42 24 42 34Z" fill="#2b2b2b"/></svg></div>
      <h3>Fugiat Nullaariatur</h3>
      <p>Aliquam venenatis lacus vitae neque gravida, eget cursus ante semper urna nisl, congue et aliquet sit amet, pulvinar sit<br>amet tortor.</p>
    </div>
    <div class="service" style="left:366px;top:146px">
      <div class="service-icon"><svg width="30" height="40" viewBox="0 0 30 40"><rect x="2" y="4" width="26" height="34" fill="#2b2b2b"/><path d="M13 8h4v3h3v4h-3v3h-4v-3h-3v-4h3z" fill="#fff"/><rect x="7" y="22" width="4" height="4" fill="#fff"/><rect x="19" y="22" width="4" height="4" fill="#fff"/><rect x="12" y="30" width="6" height="8" fill="#fff"/></svg></div>
      <h3>Fugiat Nullaariatur</h3>
      <p>Aliquam venenatis lacus vitae neque gravida, eget cursus ante semper urna nisl, congue et aliquet sit amet, pulvinar sit<br>amet tortor.</p>
    </div>
    <div class="service" style="left:714px;top:146px">
      <div class="service-icon"><svg width="34" height="38" viewBox="0 0 34 38"><circle cx="17" cy="10" r="8" fill="#2b2b2b"/><path d="M2 37 C2 22 32 22 32 37Z" fill="#2b2b2b"/><circle cx="12" cy="31" r="3" fill="none" stroke="#fff" stroke-width="2"/><circle cx="22" cy="31" r="3" fill="none" stroke="#fff" stroke-width="2"/></svg></div>
      <h3>Fugiat Nullaariatur</h3>
      <p>Aliquam venenatis lacus vitae neque gravida, eget cursus ante semper urna nisl, congue et aliquet sit amet, pulvinar sit<br>amet tortor.</p>
    </div>
    <a class="btn" style="left:435px;top:454px;width:180px;height:42px">View All Services</a>
  </div>
</section>

<section class="contact">
  <h2 class="section-title abs" style="left:75px;top:2352px;font-size:50px">Contact Us</h2>
  <p class="abs" style="left:75px;top:2428px;font-size:21px;font-weight:700;color:var(--teal);white-space:nowrap">Grey Fennel Medical</p>
  <p class="abs" style="left:75px;top:2461px;width:250px;font-size:17px;line-height:29px">Aliquam venenatis lacus vitae neque gravida</p>
  <div class="contact-line abs" style="left:75px;top:2527px"><svg width="18" height="18" viewBox="0 0 24 24"><path d="M6.6 10.8a15 15 0 0 0 6.6 6.6l2.2-2.2c.3-.3.7-.4 1-.2 1.1.4 2.3.6 3.6.6.6 0 1 .4 1 1V20c0 .6-.4 1-1 1A17 17 0 0 1 3 4c0-.6.4-1 1-1h3.5c.6 0 1 .4 1 1 0 1.3.2 2.5.6 3.6.1.3 0 .7-.2 1z" fill="var(--teal)"/></svg>1-800-555-0142</div>
  <div class="contact-line abs" style="left:75px;top:2563px"><svg width="18" height="18" viewBox="0 0 24 24"><rect x="2" y="5" width="20" height="15" rx="2" fill="var(--teal)"/><path d="M3 6 L12 13 L21 6" stroke="#fff" stroke-width="2" fill="none"/></svg>hello@greyfennelmedical.com</div>
  <a class="btn" style="left:75px;top:2622px;width:180px;height:42px">Contact Us</a>
  <div class="map abs" role="img" aria-label="Street map showing the clinic location"></div>
  <svg class="abs" style="left:852px;top:2448px" width="30" height="40" viewBox="0 0 30 40"><path d="M15 0 C6 0 0 6 0 14 C0 24 15 40 15 40 C15 40 30 24 30 14 C30 6 24 0 15 0Z" fill="#e53935"/><circle cx="15" cy="14" r="5" fill="#9b1c1c"/></svg>
</section>

<footer class="site-footer">
  <svg class="abs" style="left:0;top:2770px" width="1200" height="433" viewBox="0 0 1200 433">
    <path d="M0 70 C120 20 260 15 360 25 C520 40 620 110 760 115 C930 120 1080 100 1200 160 V433 H0Z" fill="var(--grey)"/>
    <path d="M100 40 C200 18 300 18 380 28 C530 45 630 112 770 115 C930 118 1080 100 1200 165" stroke="var(--teal)" stroke-width="12" fill="none"/>
  </svg>
  <div class="brand abs" style="left:75px;top:2980px;font-size:20px"><span class="brand-dot" style="width:30px;height:30px"></span>Grey Fennel Medical</div>
  <p class="fine abs" style="left:75px;top:3057px;width:240px">Lorem ipsum dolor sit amet, consectetur adipiscing elit, sed do eiusmod.</p>
  <div class="footer-col abs" style="left:379px;top:2940px">
    <h4>Quick Links</h4>
    <a>Home</a><a>Patients and Visitors</a><a>Health Professionals</a><a>Online Appointments</a><a>Quick links</a><a>Contact Us</a>
  </div>
  <div class="footer-col abs" style="left:647px;top:2940px">
    <h4>Services</h4>
    <a>Lorem ipsum dolor</a><a>Sit amet</a><a>Consectetur</a><a>Adipiscing elit</a><a>Sed do eiusmod</a>
  </div>
  <div class="footer-col abs" style="left:884px;top:2940px">
    <h4>Follow Us</h4>
    <div class="social" style="margin-top:10px" aria-label="Social media links"><span></span><span></span><span></span><span></span><span></span></div>
    <p class="fine" style="margin-top:38px">Copyright © 2020. Company Name<br>All rights reserved.<br>Privacy policy, Disclaimer</p>
  </div>
</footer>

</body>
</html>
```